Veranix - Solution provider in business consulting

Veranix is a swiss based company providing solutions for developing markets. The business covers various fields of business consulting, such as supply chain, product costs, quality management and manufacturing management. The Business operates in a efficient, straight and solution oriented manner.
The final design should communicate these characteristics. Asian people as well as as western people shall identify the qualities of the company at first sight.
The customer needs business cards with a simple view but an recognizable design, printed in high quality. Engraved elements such as the globe or simple words are possible.
Available colors are: (RAL)
102/102/102
51/102/102
153/204/153
255/102/51
Font: Calibri

```html
<!DOCTYPE html>
<html lang="en">
<head>
<meta charset="utf-8">
<title>Veranix – Business Card</title>
<link href="https://fonts.googleapis.com/css2?family=Carlito:wght@400;700&display=swap" rel="stylesheet">
<style>
  :root {
    --backdrop: #e4e4e2;
    --card: #f7f7f7;
    --card-edge: #ffffff;
    --ink: #666666;
    --ink-soft: #8a8a8a;
    --globe-light: #ececec;
    --globe-dark: #dddddd;
  }
  * { margin: 0; padding: 0; box-sizing: border-box; }
  html, body {
    width: 1200px;
    height: 1022px;
    overflow: hidden;
    background: var(--backdrop);
    font-family: "Carlito", "Calibri", sans-serif;
  }
  .stage {
    width: 1200px;
    height: 1022px;
    display: flex;
    align-items: center;
    justify-content: center;
  }
  .business-card {
    position: relative;
    width: 900px;
    height: 580px;
    border-radius: 22px;
    background: linear-gradient(160deg, var(--card-edge) 0%, var(--card) 55%, #efefef 100%);
    box-shadow: 0 18px 40px rgba(0,0,0,0.14);
    overflow: hidden;
    color: var(--ink);
  }
  .globe-decoration {
    position: absolute;
    left: 40px;
    top: 190px;
    width: 520px;
    height: 520px;
    border-radius: 50%;
    background: radial-gradient(circle at 45% 40%, var(--globe-light) 0%, var(--globe-dark) 100%);
    opacity: 0.7;
  }
  .brand {
    position: absolute;
    top: 120px;
    left: 0;
    right: 0;
    display: flex;
    align-items: center;
    justify-content: center;
    gap: 26px;
  }
  .brand-mark {
    width: 92px;
    height: 92px;
    border-radius: 50%;
    background: var(--ink);
  }
  .brand-name {
    font-size: 104px;
    font-weight: 400;
    letter-spacing: 2px;
    color: var(--ink);
    line-height: 1;
  }
  .details {
    position: absolute;
    left: 0;
    right: 36px;
    top: 290px;
    display: flex;
    justify-content: flex-end;
    align-items: flex-start;
    gap: 34px;
  }
  .person {
    text-align: right;
    padding-top: 42px;
  }
  .person-name {
    font-size: 28px;
    font-weight: 700;
    line-height: 1.2;
    color: var(--ink);
  }
  .person-role {
    font-size: 20px;
    line-height: 1.3;
    color: var(--ink-soft);
    margin-bottom: 24px;
  }
  .address {
    font-size: 20px;
    line-height: 1.4;
    color: var(--ink-soft);
  }
  .contacts {
    list-style: none;
    font-size: 20px;
    line-height: 1.5;
    color: var(--ink);
    white-space: nowrap;
  }
  .contacts li {
    display: flex;
    align-items: center;
    gap: 12px;
  }
  .contacts svg {
    width: 16px;
    height: 16px;
    flex: none;
    fill: none;
    stroke: var(--ink);
    stroke-width: 1.6;
  }
</style>
</head>
<body>
<main class="stage">
  <section class="business-card">
    <div class="globe-decoration" role="img" aria-label="Faint engraved globe decoration"></div>

    <header class="brand">
      <span class="brand-name">Veranix</span>
      <span class="brand-mark"></span>
    </header>

    <div class="details">
      <div class="person">
        <p class="person-name">Marten Keller</p>
        <p class="person-role">CEO</p>
        <p class="address">Veranix GmbH Lindenweg 14<br>9200 Gossau Switzerland</p>
      </div>

      <ul class="contacts">
        <li>
          <svg viewBox="0 0 16 16" aria-hidden="true"><rect x="4" y="1.5" width="8" height="13" rx="1.5"/><line x1="7" y1="12" x2="9" y2="12"/></svg>
          +41 79 508 3317
        </li>
        <li>
          <svg viewBox="0 0 16 16" aria-hidden="true"><path d="M3 2.5 L6 2.5 L7 5.5 L5.5 7 Q7 10 9 10.5 L10.5 9 L13.5 10 L13.5 13 Q7 14 2.5 6 Z"/></svg>
          +41 71 620 4481
        </li>
        <li>
          <svg viewBox="0 0 16 16" aria-hidden="true"><rect x="1.5" y="3.5" width="13" height="9" rx="1"/><polyline points="1.5,3.5 8,9 14.5,3.5"/></svg>
          marten.keller@veranix.ch
        </li>
        <li>
          <svg viewBox="0 0 16 16" aria-hidden="true"><circle cx="8" cy="8" r="6.5"/><ellipse cx="8" cy="8" rx="3" ry="6.5"/><line x1="1.5" y1="8" x2="14.5" y2="8"/></svg>
          www.veranix.ch
        </li>
      </ul>
    </div>
  </section>
</main>
</body>
</html>
```